I am a general contractor in Portland, Or. I would like a clean and simple design layout, maybe using the "didot" font, blue and dark bronze in colors are preferred. On one side of the card, it would be nice to have a logo(attached photo) and business name(KTW Construction). I don't need my job title on the card, just some thing along the lines of "gordon pike, general contractor". Thanks much.

Target Market(s)

Adults from 30-55 years old. Middle to upper class.

Industry/Entity Type

Contractor

Contact Information for Business Card

KTW Construction
Gordon L. Pike
2843 NE 71st Ave.
Portland, Or. 97288
541.555.0187

Font styles to use
Other font styles liked:
• didot

Colors
3277b5
7f7f7f

Requirements
Should not have
• Too much going on.

```html
<!DOCTYPE html>
<html lang="en">
<head>
<meta charset="utf-8">
<title>KTW Construction – Business Card</title>
<link rel="stylesheet" href="https://fonts.googleapis.com/css2?family=Exo+2:wght@400;700&display=swap">
<style>
  :root {
    --backdrop: #8f9193;
    --card: #ffffff;
    --navy: #232c6e;
    --band: #2c3f96;
    --band-light: #3550b0;
    --accent: #3a9fe0;
    --swoosh: #a9abae;
    --ink-light: #ffffff;
  }
  * { margin: 0; padding: 0; box-sizing: border-box; }
  html, body {
    width: 1200px;
    height: 771px;
    overflow: hidden;
    background: var(--backdrop);
  }
  .canvas {
    width: 1200px;
    height: 771px;
    display: flex;
    align-items: center;
    justify-content: center;
    gap: 40px;
  }
  .card {
    position: relative;
    width: 540px;
    height: 309px;
    background: var(--card);
    overflow: hidden;
    box-shadow: 0 6px 18px rgba(0,0,0,0.25);
  }

  /* Brand lockup */
  .brand {
    display: flex;
    align-items: center;
    gap: 16px;
    color: var(--navy);
    font-family: "Exo 2", sans-serif;
    font-weight: 700;
  }
  .brand-dot {
    flex: none;
    border-radius: 50%;
    background: var(--accent);
  }
  .brand-name { line-height: 1; }
  .brand-name span { display: block; }

  /* Front side */
  .card-front .brand {
    position: absolute;
    left: 50%;
    top: 50%;
    transform: translate(-50%, -50%);
  }
  .card-front .brand-dot { width: 86px; height: 86px; }
  .card-front .brand-name { font-size: 42px; }

  /* Back side */
  .card-back .band {
    position: absolute;
    inset: 0;
  }
  .card-back .brand {
    position: absolute;
    right: 60px;
    top: 26px;
    gap: 12px;
  }
  .card-back .brand-dot { width: 50px; height: 50px; }
  .card-back .brand-name { font-size: 25px; }

  .contact {
    position: absolute;
    left: 0;
    right: 0;
    top: 178px;
    display: flex;
    align-items: center;
    color: var(--ink-light);
    font-family: "Exo 2", sans-serif;
    font-size: 10.5px;
    letter-spacing: 1.6px;
  }
  .contact-person {
    width: 262px;
    text-align: right;
    padding-right: 14px;
    line-height: 1.55;
  }
  .person-name {
    font-size: 12.5px;
    font-weight: 700;
    letter-spacing: 2.4px;
    text-transform: uppercase;
  }
  .person-role { margin-bottom: 10px; }
  .contact-divider {
    width: 1px;
    height: 104px;
    background: rgba(255,255,255,0.75);
  }
  .contact-lines {
    list-style: none;
    padding-left: 12px;
    line-height: 1.45;
  }
  .contact-lines li {
    display: flex;
    align-items: center;
    gap: 7px;
  }
  .contact-lines svg { flex: none; }
</style>
</head>
<body>
<main class="canvas">

  <section class="card card-front" aria-label="Card front">
    <div class="brand">
      <div class="brand-dot"></div>
      <div class="brand-name"><span>KTW</span><span>Construction</span></div>
    </div>
  </section>

  <section class="card card-back" aria-label="Card back">
    <svg class="band" width="540" height="309" viewBox="0 0 540 309" aria-hidden="true">
      <defs>
        <linearGradient id="bandFill" x1="0" y1="0" x2="1" y2="1">
          <stop offset="0" stop-color="var(--navy)"/>
          <stop offset="1" stop-color="var(--band-light)"/>
        </linearGradient>
      </defs>
      <path d="M0,92 C160,82 300,120 540,196 L540,212 C300,140 160,104 0,112 Z" fill="var(--swoosh)"/>
      <path d="M0,120 C170,110 310,150 540,222 L540,309 L0,309 Z" fill="url(#bandFill)"/>
    </svg>

    <div class="brand">
      <div class="brand-dot"></div>
      <div class="brand-name"><span>KTW</span><span>Construction</span></div>
    </div>

    <div class="contact">
      <div class="contact-person">
        <div class="person-name">Gordon Pike</div>
        <div class="person-role">General Contractor</div>
        <div>2843 NE 71st Ave.</div>
        <div>Portland, Or. 97288</div>
      </div>
      <div class="contact-divider"></div>
      <ul class="contact-lines">
        <li>
          <svg width="11" height="11" viewBox="0 0 12 12" aria-hidden="true"><circle cx="6" cy="6" r="6" fill="#fff"/><path d="M3.6,3.2 L5,3 L5.6,4.6 L4.8,5.2 C5.2,6 6,6.8 6.8,7.2 L7.4,6.4 L9,7 L8.8,8.4 C6,8.6 3.4,6 3.6,3.2 Z" fill="var(--band)"/></svg>
          541.555.0187
        </li>
      </ul>
    </div>
  </section>

</main>
</body>
</html>
```